Tech business card design

We need an amazing business card design for our new business 'Pexla' a marketing tech startup based in Sydney, Australia. We provide an online marketplace for businesses to search and buy advertising media, connect with service providers and learn more about marketing. We wish to communicate 'cool tech', reliability and professionalism and design based around our logo.

Target Market(s)

Business Owners

Contact Information for Business Card

Name
Position
Email Address
Website
Phone Number

Font styles to use
Other font styles liked:
• Avenir & Avenir Next

Colors

Designer to choose colors to be used in the design.

```html
<!DOCTYPE html>
<html lang="en">
<head>
<meta charset="utf-8">
<title>Pexla Business Card</title>
<link rel="stylesheet" href="https://fonts.googleapis.com/css2?family=Arimo:wght@400;700&display=swap">
<style>
  :root {
    --backdrop: #2a2a2a;
    --card-white: #ffffff;
    --navy: #1b1f4b;
    --grey: #6b6c6f;
    --grey-light: #808184;
    --divider: #b9b9bc;
    --ink: #1d1d1f;
  }
  * { box-sizing: border-box; margin: 0; padding: 0; }
  html, body {
    width: 1200px; height: 900px; overflow: hidden;
    background: var(--backdrop);
    font-family: "Arimo", Arial, sans-serif;
  }
  .canvas { position: relative; width: 1200px; height: 900px; }
  .card {
    position: absolute; left: 250px; width: 700px; height: 400px;
    border-radius: 36px; overflow: hidden;
  }
  .card-front { top: 40px; background: var(--card-white); }
  .card-back { top: 470px; background: var(--grey); }
  .swoosh { position: absolute; inset: 0; }
  .wordmark {
    position: absolute; font-weight: 700; color: var(--navy);
    letter-spacing: -2px; line-height: 1;
  }
  .card-front .wordmark { left: 60px; top: 140px; font-size: 92px; }
  .card-back .wordmark {
    left: 0; right: 0; top: 140px; text-align: center; font-size: 130px;
  }
  .divider {
    position: absolute; left: 385px; top: 55px; width: 1px; height: 195px;
    background: var(--divider);
  }
  .contact { position: absolute; left: 415px; top: 62px; color: var(--ink); }
  .contact-name { font-size: 21px; font-weight: 700; color: var(--navy); }
  .contact-role { font-size: 15px; font-weight: 700; color: var(--navy); margin: 2px 0 14px 10px; }
  .contact-address { font-size: 15px; line-height: 19px; margin: 0 0 14px 10px; }
  .contact-list { list-style: none; font-size: 15px; line-height: 22px; }
  .contact-list li { display: flex; align-items: center; gap: 10px; }
  .contact-list svg { width: 13px; height: 13px; flex: none; }
</style>
</head>
<body>
<main class="canvas">
  <section class="card card-front" aria-label="Card front">
    <svg class="swoosh" viewBox="0 0 700 400" aria-hidden="true">
      <path fill="var(--grey-light)" d="M0,322 C220,318 480,300 700,268 L700,282 C480,322 250,345 0,352 Z"/>
      <path fill="var(--navy)" d="M0,350 C250,343 480,322 700,280 L700,292 C500,345 260,385 110,400 L0,400 Z"/>
    </svg>
    <div class="wordmark">Pexla</div>
    <div class="divider"></div>
    <div class="contact">
      <p class="contact-name">JOHN SMITH</p>
      <p class="contact-role">Position</p>
      <p class="contact-address">Street Name, City Name<br>Zipcode:012345</p>
      <ul class="contact-list">
        <li>
          <svg viewBox="0 0 16 16"><path fill="var(--ink)" d="M3 1l3 3-2 2c1 2 3 4 5 5l2-2 3 3-2 2C7 14 2 9 1 3z"/></svg>
          012-345-6789
        </li>
        <li>
          <svg viewBox="0 0 16 16"><rect x="1" y="3" width="14" height="10" fill="var(--ink)"/><path d="M1 3l7 6 7-6" fill="none" stroke="#fff" stroke-width="1.5"/></svg>
          info@pexla.com
        </li>
        <li>
          <svg viewBox="0 0 16 16" fill="none" stroke="var(--ink)" stroke-width="1.4"><circle cx="8" cy="8" r="6.5"/><ellipse cx="8" cy="8" rx="3" ry="6.5"/><path d="M1.5 8h13"/></svg>
          www.pexla.com
        </li>
      </ul>
    </div>
  </section>

  <section class="card card-back" aria-label="Card back">
    <div class="wordmark">Pexla</div>
  </section>
</main>
</body>
</html>
```